NZ First of it's kind solutions directory and marketplace for busy Mums needs a business card design

We need a business card design for our new nationwide business in NZ (long term plans to go global). We provide solutions to the everyday challenges that busy Mums face by connecting them with quality communities and suppliers of carefully selected, relevant products and services. We sell direct via our online marketplace. The final design should communicate our values of inclusivity, quality and smart solutions. Colours should incorporate our logo colour palette of #477077 and #6ba8b2. Our website is at https://www.brightnestmums.example

Target Market(s)

busy Mums, Age 28 – 50, female, income over $100K, location main centres NZ primarily but NZ wide. Is likely juggling work or career with a young family. Probably had hobbies which have fallen by the wayside.
-Wants to succeed in her chosen career without compromising on family life
-to successfully juggle her career without feeling like she is compromising her children
- Is time poor, something always has to give and it’s generally her health (she’ll stay up late, get stressed)
- probably ex corporate or professional career. Has discretional income

Industry/Entity Type

Business

Contact Information for Business Card

Lena Forbisher, Founder, BrightNestMums.example (Strapline Tap; Gather; Sorted), 47 Kowhai Terrace, Ellerslie, Auckland 1051, New Zealand. Mob: 021 483 517 Ph: +64 (0)9 571 4860

Font styles to use
Other font styles liked:
• Raleway, and/or Architects Daughter

Colors
00a990
33b8a4
86cfc6
cfeae6

Requirements
Must have
• the above details, streamline. the logo and colours associated with those logos
Should not have
• foil or metallic colours

```html
<!DOCTYPE html>
<html lang="en">
<head>
<meta charset="utf-8">
<title>BrightNestMums Business Card</title>
<link href="https://fonts.googleapis.com/css2?family=Raleway:wght@400;500;700;800&display=swap" rel="stylesheet">
<style>
  :root {
    --teal-dark: #477077;
    --teal-light: #6ba8b2;
    --white: #ffffff;
    --backdrop: #2b2d2e;
  }
  * { margin: 0; padding: 0; box-sizing: border-box; }
  html, body {
    width: 1189px;
    height: 1200px;
    overflow: hidden;
    background: var(--backdrop);
    font-family: "Raleway", Arial, sans-serif;
  }
  .card {
    position: absolute;
    left: 148px;
    width: 892px;
    height: 508px;
    border-radius: 34px;
    overflow: hidden;
  }
  .card-front { top: 55px; background: var(--teal-light); }
  .card-back { top: 637px; background: var(--white); }

  /* Front */
  .front-brand {
    position: absolute;
    top: 222px;
    left: 0;
    width: 100%;
    display: flex;
    justify-content: center;
    align-items: center;
    gap: 18px;
  }
  .brand-dot {
    width: 46px;
    height: 46px;
    border-radius: 50%;
    flex: none;
  }
  .front-brand .brand-dot { background: var(--white); }
  .front-brand .brand-name {
    font-weight: 800;
    font-size: 58px;
    color: var(--white);
    letter-spacing: -1px;
    line-height: 1;
  }
  .front-url {
    position: absolute;
    top: 365px;
    width: 100%;
    text-align: center;
    color: var(--white);
    font-size: 19px;
    letter-spacing: 3px;
  }
  .front-url strong { font-weight: 700; }

  /* Back */
  .back-brand {
    position: absolute;
    top: 88px;
    left: 44px;
    display: flex;
    align-items: center;
    gap: 16px;
  }
  .back-brand .brand-dot { background: var(--teal-dark); width: 52px; height: 52px; }
  .back-brand .brand-name {
    font-weight: 800;
    font-size: 52px;
    color: var(--teal-dark);
    letter-spacing: -1px;
    line-height: 1;
  }
  .social-row {
    position: absolute;
    top: 44px;
    left: 634px;
    display: flex;
    gap: 6px;
  }
  .social-dot {
    width: 37px;
    height: 37px;
    border-radius: 50%;
    background: var(--teal-dark);
  }
  .strapline {
    position: absolute;
    top: 228px;
    left: 44px;
    font-size: 20px;
    color: var(--teal-light);
  }
  .contact-bands {
    position: absolute;
    left: 0;
    top: 0;
    width: 892px;
    height: 508px;
  }
  .person {
    position: absolute;
    top: 302px;
    left: 44px;
    color: var(--white);
  }
  .person-name { font-weight: 800; font-size: 28px; line-height: 1; letter-spacing: -0.5px; }
  .person-role { font-size: 20px; line-height: 1.2; }
  .phones {
    position: absolute;
    top: 406px;
    left: 44px;
    color: var(--white);
    font-size: 21px;
    line-height: 28px;
  }
  .phone-line { display: flex; align-items: center; gap: 8px; }
  .phone-line svg { width: 22px; height: 22px; flex: none; }
  .address {
    position: absolute;
    top: 346px;
    left: 598px;
    color: var(--white);
    font-size: 21px;
    line-height: 28px;
  }
  .back-url {
    position: absolute;
    top: 462px;
    right: 50px;
    color: var(--white);
    font-size: 21px;
  }
</style>
</head>
<body>

<section class="card card-front">
  <div class="front-brand">
    <span class="brand-dot"></span>
    <span class="brand-name">BrightNestMums</span>
  </div>
  <p class="front-url">www.<strong>brightnestmums</strong>.example</p>
</section>

<section class="card card-back">
  <div class="back-brand">
    <span class="brand-dot"></span>
    <span class="brand-name">BrightNestMums</span>
  </div>

  <div class="social-row">
    <span class="social-dot"></span>
    <span class="social-dot"></span>
    <span class="social-dot"></span>
    <span class="social-dot"></span>
    <span class="social-dot"></span>
  </div>

  <p class="strapline">Solutions for Busy Mums. Tap, Gather, Sorted.</p>

  <svg class="contact-bands" viewBox="0 0 1049 598" preserveAspectRatio="none" aria-hidden="true">
    <rect x="0" y="338" width="1049" height="260" fill="var(--teal-dark)"/>
    <path d="M0 446 L400 446 C440 446 445 396 490 396 L1049 396 L1049 525 L650 525 C610 525 610 576 570 576 L0 576 Z" fill="var(--teal-light)"/>
  </svg>

  <div class="person">
    <p class="person-name">Lena Forbisher</p>
    <p class="person-role">Founder</p>
  </div>

  <div class="phones">
    <p class="phone-line">
      <svg viewBox="0 0 22 22" aria-hidden="true">
        <circle cx="11" cy="11" r="10" fill="none" stroke="var(--white)" stroke-width="1.5"/>
        <rect x="7.5" y="5" width="7" height="12" rx="1.2" fill="none" stroke="var(--white)" stroke-width="1.4"/>
        <line x1="10" y1="14.8" x2="12" y2="14.8" stroke="var(--white)" stroke-width="1.2"/>
      </svg>
      <span>021 483 517</span>
    </p>
    <p class="phone-line">
      <svg viewBox="0 0 22 22" aria-hidden="true">
        <circle cx="11" cy="11" r="10" fill="none" stroke="var(--white)" stroke-width="1.5"/>
        <path d="M5.5 9 C5.5 6.5 16.5 6.5 16.5 9 L14.5 10 L13.5 8.6 L8.5 8.6 L7.5 10 Z" fill="var(--white)"/>
        <rect x="7" y="10.5" width="8" height="5.5" rx="1" fill="var(--white)"/>
      </svg>
      <span>+64 (0)9 571 4860</span>
    </p>
  </div>

  <address class="address" style="font-style: normal;">
    47 Kowhai Terrace,<br>
    Ellerslie, Auckland 1051<br>
    New Zealand
  </address>

  <p class="back-url">www.brightnestmums.example</p>
</section>

</body>
</html>
```